Catering Menu Package

I currently have a complete menu package, which we have redesigned as far as content, now I need to it put together in a catalog type format. It is essentially 10-12 pages in length, and will be sent for print production. Upon receiving a final edit
Updates

I have added an example gif to the project.

I did this free hand this basically what I am looking for. please change text and type to whatever you think would look best. This is a total rough design so, feel free to change any and everything. The text for the page is on the word documents. If you need more images let me know I am in the process of getting as many images uploaded for your use.

Project Deadline Extended
Reason: I figured we got a late jump with questions, so i am extending a few days .

Target Market(s)

The target market is business who wish to have catered luncheons, breakfasts , meetings

Industry/Entity Type

Catering

Requirements
Must have
• I have attached a copy of the text that what we want in the package, our logo, and i have also attached a catering package of another company to give you an idea what the finished product will be
Should not have
• It should not look identical to the example catering packages, these are for some inspiration we want our own design with the same type of look and feel

```html
<!DOCTYPE html>
<html lang="en">
<head>
<meta charset="utf-8">
<title>Catering Menu – Mix &amp; Mingle / Office Party</title>
<link href="https://fonts.googleapis.com/css2?family=Pinyon+Script&family=Gabriela&display=swap" rel="stylesheet">
<style>
  :root {
    --paper: #ebe6db;
    --paper-deep: #e3ddd0;
    --ink: #1a1917;
    --rule: #141414;
  }
  html, body {
    margin: 0;
    padding: 0;
    width: 1200px;
    height: 928px;
    overflow: hidden;
    background: var(--paper);
  }
  .menu-spread {
    position: relative;
    width: 1200px;
    height: 928px;
    overflow: hidden;
    color: var(--ink);
    font-family: "Gabriela", Georgia, serif;
  }
  .menu-spread__texture {
    position: absolute;
    inset: 0;
    background: radial-gradient(ellipse at 50% 50%, var(--paper) 0%, var(--paper-deep) 100%);
  }
  .menu-column {
    position: absolute;
    top: 120px;
  }
  .menu-column--left { left: 32px; }
  .menu-column--right { left: 640px; width: 440px; }
  .menu-column__title {
    margin: 0 0 2px 0;
    font-family: "Pinyon Script", cursive;
    font-weight: 400;
    font-size: 50px;
    line-height: 62px;
    letter-spacing: 0.5px;
  }
  .menu-list {
    list-style: none;
    margin: 0;
    padding: 0;
  }
  .menu-list li {
    font-size: 16.5px;
    line-height: 31.8px;
    white-space: nowrap;
    letter-spacing: -0.2px;
  }
  .menu-list li.wrap { white-space: normal; }
  .menu-divider {
    position: absolute;
    left: 611px;
    top: 138px;
    width: 3px;
    height: 695px;
    background: var(--rule);
  }
</style>
</head>
<body>
<main class="menu-spread">
  <div class="menu-spread__texture" role="img" aria-label="Soft cream background with a faint swirling floral damask pattern"></div>

  <section class="menu-column menu-column--left">
    <h2 class="menu-column__title">The Mix &amp; Mingle</h2>
    <ul class="menu-list">
      <li>Scallops Wrapped in Bacon</li>
      <li>Shrimp Cocktail</li>
      <li>Thai Grilled Chicken Bites</li>
      <li>Served with steamed wild rice</li>
      <li>Marinated Flank Steak</li>
      <li>Carved and served with herb mayonnaise &amp; horseradish</li>
      <li>With fresh rolls &amp; Artisan bread</li>
      <li>Aged Cheese Board</li>
      <li>Pepper Jack, Smoked Gouda, English Cheddar</li>
      <li>Goat, Gorgonzola &amp; Aged Swiss</li>
      <li>Garnished with dried fruit &amp; nuts</li>
      <li>Served with crackers</li>
      <li>Mediterranean Pasta Salad</li>
      <li>Fresh Fruit &amp; Melon Display</li>
    </ul>
  </section>

  <div class="menu-divider" aria-hidden="true"></div>

  <section class="menu-column menu-column--right">
    <h2 class="menu-column__title">The Office Party</h2>
    <ul class="menu-list">
      <li>Grilled Marinated London Broil</li>
      <li>Carved and served with horseradish &amp; port wine mush-</li>
      <li>room sauce</li>
      <li>Grilled Whole Mahi Mahi Display</li>
      <li>Served with fruit salsa</li>
      <li>Southwest Twice Baked Potato Bites</li>
      <li>Stuffed with scallions, bacon, cheese, butter &amp; sour cream</li>
      <li>Balsamic Fire Roasted Vegetable Medley</li>
      <li>Fresh Baked Rolls &amp; Artisan Bread</li>
      <li>Served with whipped butter</li>
      <li>Bite Sized Italian Sausage</li>
      <li>With peppers &amp; onions</li>
      <li>With condiments &amp; fresh baked rolls</li>
      <li>Buffalo Drummies &amp; Wing Sections</li>
      <li>Served with bleu cheese dressing, celery &amp; carrot sticks</li>
      <li>Queso Dip</li>
      <li>Served with tortilla chips</li>
    </ul>
  </section>
</main>
</body>
</html>
```